Wedding Invitations

We are a printing company "inkhollow" and require multiple wedding invitation designs for our customers in store and online. We would like the designs to be editable in Photoshop if possible, if not then a layout with suggested fonts would be the next best option. We are open to suggestions on design but would like to stick to the general wedding themes some with a modern and some with a classical feel

Industry/Entity Type

Printing

```html
<!DOCTYPE html>
<html lang="en">
<head>
<meta charset="utf-8">
<title>Wedding Invitation – Clara &amp; Oliver</title>
<link rel="stylesheet" href="https://fonts.googleapis.com/css2?family=Cinzel:wght@400;500&family=Playfair+Display:ital@1&family=Questrial&display=swap">
<style>
  :root {
    --paper-blue: #809fc3;
    --lace-light: #b9cce2;
    --lace-mid: #9bb4d2;
    --ink: #111418;
    --white: #ffffff;
  }
  * { margin: 0; padding: 0; box-sizing: border-box; }
  html, body { width: 1200px; height: 857px; overflow: hidden; background: var(--paper-blue); }
  .invitation {
    position: relative;
    width: 1200px;
    height: 857px;
    background: var(--paper-blue);
    color: var(--ink);
    overflow: hidden;
  }
  .lace-pattern {
    position: absolute;
    inset: 0;
    background:
      radial-gradient(ellipse 300px 460px at 150px 380px, rgba(185,204,226,0.55), rgba(155,180,210,0) 75%),
      radial-gradient(ellipse 360px 480px at 1060px 460px, rgba(185,204,226,0.55), rgba(155,180,210,0) 75%),
      radial-gradient(ellipse 260px 200px at 720px 60px, rgba(185,204,226,0.35), rgba(155,180,210,0) 75%),
      radial-gradient(ellipse 280px 200px at 560px 820px, rgba(185,204,226,0.35), rgba(155,180,210,0) 75%);
  }
  .text-block { position: absolute; left: 0; width: 100%; text-align: center; }
  .intro {
    top: 142px;
    font-family: "Playfair Display", serif;
    font-style: italic;
    font-size: 25px;
  }
  .name {
    font-family: "Cinzel", serif;
    font-weight: 500;
    font-size: 50px;
    letter-spacing: 1px;
  }
  .name-bride { top: 186px; }
  .name-groom { top: 312px; }
  .conjunction {
    top: 236px;
    font-family: "Playfair Display", serif;
    font-style: italic;
    font-size: 62px;
    color: var(--white);
  }
  .request {
    top: 436px;
    font-family: "Cinzel", serif;
    font-size: 22px;
    letter-spacing: 0.5px;
  }
  .details {
    position: absolute;
    top: 530px;
    font-family: "Questrial", sans-serif;
    font-size: 23px;
    line-height: 31px;
    letter-spacing: 0.5px;
  }
  .details-date { right: 626px; text-align: right; }
  .details-venue { left: 674px; text-align: left; }
  .divider {
    position: absolute;
    left: 616px;
    top: 495px;
    width: 2px;
    height: 143px;
    background: var(--white);
  }
  .closing {
    top: 658px;
    font-family: "Playfair Display", serif;
    font-style: italic;
    font-size: 25px;
  }
</style>
</head>
<body>
  <main class="invitation">
    <div class="lace-pattern" role="img" aria-label="Soft white floral lace pattern across the blue background"></div>

    <p class="text-block intro">Together with their families</p>
    <h1 class="text-block name name-bride">Clara Rose Whitfield</h1>
    <p class="text-block conjunction">and</p>
    <h1 class="text-block name name-groom">Oliver James Hartley</h1>

    <p class="text-block request">Request the pleasure of your company as they are united in marriage</p>

    <p class="details details-date">Saturday Tenth September<br>Two Thousand Thirteen<br>Two O'Clock in the evening</p>
    <div class="divider"></div>
    <p class="details details-venue">St Aldric's Chapel<br>128 Willow Lane<br>Ashford TN24 8QP</p>

    <p class="text-block closing">dinner and dancing to follow</p>
  </main>
</body>
</html>
```